Carpet cleaning company focused on high quality needs business cards

We are a growing company that just merged with another company and need to design a new business card. We do both residential as well as commercial cleaning. We do carpet, tile & grout, upholstery, hard floors, and stain & pet odor removal. We treat our customers like family and strive to achieve outstanding results with every job.

```html
<!DOCTYPE html>
<html lang="en">
<head>
<meta charset="utf-8">
<title>Brightwell Floor Care – Business Card</title>
<link href="https://fonts.googleapis.com/css2?family=Open+Sans:wght@400;600;700&display=swap" rel="stylesheet">
<style>
  :root {
    --bg: #d6d6d6;
    --card: #ffffff;
    --ink: #1a1a1a;
    --brand-blue: #0d4fa3;
    --accent-blue: #0c82c4;
    --brand-red: #ee4037;
    --muted: #333333;
  }
  * { margin: 0; padding: 0; box-sizing: border-box; }
  html, body { width: 1200px; height: 588px; overflow: hidden; }
  body {
    background: var(--bg);
    font-family: "Open Sans", Arial, sans-serif;
    position: relative;
  }
  .card {
    position: absolute;
    width: 488px;
    height: 289px;
    background: var(--card);
    border-radius: 22px;
    overflow: hidden;
  }
  .card--front { left: 87px; top: 141px; }
  .card--back { left: 622px; top: 142px; }

  .info-band {
    position: absolute; left: 0; right: 0; top: 148px; bottom: 0;
    background: linear-gradient(180deg, #202020 0%, #151515 100%);
    border-top: 4px solid var(--accent-blue);
  }

  .brand { position: absolute; display: flex; align-items: center; }
  .brand__dot { background: var(--brand-red); border-radius: 50%; flex: none; }
  .brand__name { font-weight: 700; color: var(--ink); line-height: 1.1; }
  .brand--small { left: 24px; top: 70px; }
  .brand--small .brand__dot { width: 22px; height: 22px; margin-right: 10px; }
  .brand--small .brand__name { font-size: 22px; }

  .brand--large { left: 0; right: 0; top: 124px; justify-content: center; }
  .brand--large .brand__dot { width: 34px; height: 34px; margin-right: 16px; }
  .brand--large .brand__name { font-size: 34px; }

  .person { position: absolute; right: 23px; top: 20px; text-align: right; }
  .person__name { color: var(--brand-blue); font-weight: 700; font-size: 20px; line-height: 1.1; letter-spacing: -0.2px; }
  .person__role { color: var(--muted); font-size: 14px; line-height: 1.2; }
  .accent-bar { position: absolute; right: 0; top: 22px; width: 12px; height: 33px; background: var(--brand-blue); }

  .address {
    position: absolute; right: 23px; top: 163px;
    color: #fff; font-size: 14px; line-height: 17px; text-align: right;
  }
  .contacts { position: absolute; right: 8px; top: 218px; list-style: none; }
  .contacts li {
    display: flex; align-items: center; justify-content: flex-end;
    color: #fff; font-size: 14px; line-height: 17.5px;
  }
  .contacts svg { width: 11px; height: 11px; margin-left: 7px; fill: var(--accent-blue); }
</style>
</head>
<body>
  <section class="card card--front">
    <div class="info-band" role="img" aria-label="Dark contact band with blue and red accent swoosh"></div>

    <div class="brand brand--small">
      <span class="brand__dot"></span>
      <p class="brand__name">Brightwell Floor Care</p>
    </div>

    <div class="person">
      <p class="person__name">MARCUS BELL</p>
      <p class="person__role">OWNER</p>
    </div>
    <span class="accent-bar"></span>

    <p class="address">Your address, City<br>State, Zip 1234</p>
    <ul class="contacts">
      <li>123 456 00000
        <svg viewBox="0 0 24 24"><path d="M6.6 10.8a15.1 15.1 0 0 0 6.6 6.6l2.2-2.2a1 1 0 0 1 1-.25 11.4 11.4 0 0 0 3.6.57 1 1 0 0 1 1 1V20a1 1 0 0 1-1 1A17 17 0 0 1 3 4a1 1 0 0 1 1-1h3.5a1 1 0 0 1 1 1c0 1.25.2 2.45.57 3.57a1 1 0 0 1-.25 1z"/></svg>
      </li>
      <li>info@yourgmail.com
        <svg viewBox="0 0 24 24"><rect x="2" y="5" width="20" height="14" rx="1"/><path d="M2 6l10 7 10-7" fill="none" stroke="#171717" stroke-width="2"/></svg>
      </li>
      <li>www.yourwebsite.com
        <svg viewBox="0 0 24 24"><circle cx="12" cy="12" r="10"/></svg>
      </li>
    </ul>
  </section>

  <section class="card card--back">
    <div class="brand brand--large">
      <span class="brand__dot"></span>
      <p class="brand__name">Brightwell Floor Care</p>
    </div>
  </section>
</body>
</html>
```